Business Cards

I am a landscape designer and I am hired to do over the top landscapes!
I pay attention to detail and do everything from growing my own orchids and Fruits and Vegetables.
I build ponds water features. I do Landscape Lighting and Specialize in Drip Irrigation for New Landscapes.
I am looking for something with a picture of one of my landscapes and pictures of Orchids on the back so I can work on growing my Orchid business.
I like the plastic cards.
I like Saturation
I like color and I want something that really sticks out!
I will attach a few pics!
Thanks
Corey
A Verdant Terrace LLC
Corey Halvorsen
Orchids & Organic Farming
Landscaping Made Simple
561-555-0147
Averdantterrace@mailbrook.net
Palm Hollow Bay FL

Target Market(s)

I work for Wealthy Clients who want unique designs and enjoy rare plants.
I am the goto guy for tropical and rare plants
Cool Designs
Orchids
Interior Decorating
Exterior Lighting
Organic Farming
People who appreciate plants

Industry/Entity Type

Landscape

Font styles to use
Decorative

Requirements
Must have
• COLOR COLOR COLOR
Saturation
Sleek and Clean
Should not have
• tacky

```html
<!DOCTYPE html>
<html lang="en">
<head>
<meta charset="utf-8">
<title>A Verdant Terrace LLC — Business Card</title>
<link href="https://fonts.googleapis.com/css2?family=Bebas+Neue&display=swap" rel="stylesheet">
<style>
  :root{
    --backdrop:#ece6de;
    --leaf-dark:#0f4a12;
    --leaf-mid:#2f8a1e;
    --leaf-light:#6fc23a;
    --white:#ffffff;
    --gold:#f2c51a;
    --lime:#6ee01e;
    --ink:#0c0708;
    --orchid-magenta:#d21c9a;
    --orchid-yellow:#f3d21a;
    --orchid-violet:#5a22d8;
    --orchid-orange:#f2631c;
  }
  *{margin:0;padding:0;box-sizing:border-box}
  html,body{width:1200px;height:900px;overflow:hidden}
  body{background:var(--backdrop);position:relative;font-family:"Bebas Neue",sans-serif;}
  .card{position:absolute;left:273px;width:649px;height:368px;overflow:hidden;box-shadow:0 3px 10px rgba(0,0,0,.25)}
  .card--front{top:48px}
  .card--back{top:483px;background:var(--ink)}
  .foliage-photo{position:absolute;inset:0;
    background:
      radial-gradient(ellipse at 30% 25%, var(--leaf-light) 0%, transparent 45%),
      radial-gradient(ellipse at 75% 80%, var(--leaf-light) 0%, transparent 40%),
      linear-gradient(135deg, var(--leaf-mid), var(--leaf-dark) 55%, var(--leaf-mid));}
  .brand-line{position:absolute;right:22px;color:var(--white);line-height:1;white-space:nowrap;text-align:right;letter-spacing:1px}
  .brand-line--one{top:20px;font-size:122px}
  .brand-line--two{top:110px;font-size:122px}
  .brand-line--llc{top:216px;font-size:128px}
  .tagline{position:absolute;right:160px;top:226px;color:var(--white);font-size:34px;line-height:1;text-align:right;letter-spacing:1.5px;white-space:nowrap}
  .services{position:absolute;left:18px;right:18px;top:321px;color:var(--gold);font-size:24px;line-height:1;letter-spacing:1px;display:flex;justify-content:center;gap:12px;white-space:nowrap}
  .orchid-photo{position:absolute}
  .orchid-photo--magenta{left:0;top:0;width:216px;height:245px;background:linear-gradient(160deg,#e23cb4,var(--orchid-magenta) 50%,#9a8a3a)}
  .orchid-photo--yellow{left:216px;top:0;width:217px;height:122px;background:radial-gradient(circle at 45% 50%,var(--orchid-yellow) 40%,#e8801a 90%)}
  .orchid-photo--violet{left:216px;top:122px;width:217px;height:123px;background:linear-gradient(135deg,#7a3cf0,var(--orchid-violet) 60%,#3a1a9a)}
  .orchid-photo--orange{left:433px;top:0;width:216px;height:245px;background:radial-gradient(circle at 50% 55%,#f0a03a,var(--orchid-orange) 55%,#d8306a)}
  .holder{position:absolute;right:18px;top:248px;color:var(--white);font-size:64px;line-height:1;letter-spacing:.5px;white-space:nowrap}
  .contact{position:absolute;right:18px;color:var(--lime);font-size:21px;line-height:1;letter-spacing:.8px;text-align:right;white-space:nowrap}
  .contact--direct{top:309px}
  .contact--place{top:332px}
  .contact span+span{margin-left:14px}
</style>
</head>
<body>
  <section class="card card--front">
    <div class="foliage-photo" role="img" aria-label="Close-up photo of striped tropical green foliage"></div>
    <div class="brand-line brand-line--one">A VERDANT</div>
    <div class="brand-line brand-line--two">TERRACE</div>
    <div class="tagline">WE MAKE YOUR GARDEN<br>BOLD AND BEAUTIFUL!</div>
    <div class="brand-line brand-line--llc">LLC</div>
    <div class="services"><span>LANDSCAPE DESIGN &amp; BUILD</span><span>•</span><span>LANDSCAPE LIGHTING &amp; DRIP IRRIGATION</span></div>
  </section>

  <section class="card card--back">
    <div class="orchid-photo orchid-photo--magenta" role="img" aria-label="Photo of magenta orchid blooms"></div>
    <div class="orchid-photo orchid-photo--yellow" role="img" aria-label="Photo of a yellow orchid bloom"></div>
    <div class="orchid-photo orchid-photo--violet" role="img" aria-label="Photo of violet orchid blooms"></div>
    <div class="orchid-photo orchid-photo--orange" role="img" aria-label="Photo of orange orchid blooms"></div>
    <div class="holder">COREY HALVORSEN</div>
    <div class="contact contact--direct"><span>T. 561-555-0147</span><span>E. AVERDANTTERRACE@MAILBROOK.NET</span></div>
    <div class="contact contact--place">PALM HOLLOW BAY FL</div>
  </section>
</body>
</html>
```